Web landing page design

- Create a Web Design (Uncoded - PSD layout only)

We need a single web page design to promote our service. This page will
acts as a landing page for users and also be utilized in social media
advertising. Please provide us with a cutting edge design. I have attached
a link for what the company is about. In essence we are a photo checking
service which reviews photos for retailers, hotels abd car dealerships to
check everything is good after a service has been performed. Whether it be
a new promotion, cleaning or just checking prices. I am looking for a
design to say that we do many photos and at a very cost effective price
(team based in Mexico)

Link: https://slidevault.example/view/qTr8nWx2LpZk4mHcYdJs/
*Deadline*
5 days
*Updates*

- The Start Here box needs to look like this:

-Start Here (heading)
-A box for email addresses to be entered
-Then a check box with "Yes, I have read and agree to the Privacy Policy
and agree to receive email marketing from Plumora88'
-A submit button

All of this information needs to be in one box please. And please feel
free to contact me if you have any questions about this.

*Target Market(s)*
Retail business, Merchandising companies, Rental property owners, Car
dealers
Updates

Please can you submit entries. I am just looking for a tidy to a presentation already created. Just needs design touches.

Target Market(s)

Ability for audience to understand concept quickly
Benefits to why to use the product stand out
Technology driven approach

Industry/Entity Type

Retail

Number of Pages Required

1 page

Colors
0792cd

Requirements
Must have
• Clean and modern design

```html
<!DOCTYPE html>
<html lang="en">
<head>
<meta charset="utf-8">
<title>Checkora – Photo Verification for Retail</title>
<link rel="stylesheet" href="https://fonts.googleapis.com/css2?family=Montserrat:wght@400;500;600;700&family=Open+Sans:wght@400&display=swap">
<style>
  :root {
    --brand-blue: #1580c4;
    --brand-blue-dark: #0d66a8;
    --ink-dark: #1c1c1e;
    --footer-bg: #2a2a2a;
    --ring-fill: #e3eff8;
    --ring-track: #9dc3df;
    --number-blue: #1b78ba;
    --white: #ffffff;
    --form-bg: rgba(236, 234, 238, 0.93);
    --form-text: #555;
  }
  * { box-sizing: border-box; margin: 0; padding: 0; }
  html, body { width: 1200px; height: 1049px; overflow: hidden; }
  body { font-family: "Montserrat", sans-serif; background: var(--ink-dark); position: relative; }

  .top-rule { position: absolute; top: 0; left: 0; width: 1200px; height: 4px; background: var(--brand-blue); z-index: 3; }

  .hero-photo {
    position: absolute; top: 0; left: 0; width: 1200px; height: 699px;
    background:
      radial-gradient(ellipse 260px 180px at 960px 300px, rgba(214,150,110,0.75), transparent 70%),
      radial-gradient(ellipse 240px 150px at 820px 560px, rgba(190,130,95,0.7), transparent 70%),
      radial-gradient(ellipse 200px 160px at 60px 330px, rgba(210,150,70,0.45), transparent 70%),
      radial-gradient(ellipse 280px 200px at 300px 600px, rgba(80,70,110,0.55), transparent 70%),
      linear-gradient(160deg, #2a2624 0%, #4a3d38 35%, #3a3230 60%, #1e1c1f 100%);
  }

  .site-header { position: absolute; top: 0; left: 0; width: 1200px; height: 160px; z-index: 2; }
  .brand { position: absolute; left: 99px; top: 56px; display: flex; align-items: center; gap: 10px; }
  .brand-dot { width: 34px; height: 34px; border-radius: 50%; background: var(--brand-blue); }
  .brand-name { font-size: 40px; font-weight: 700; color: var(--white); letter-spacing: 0.5px; }
  .main-nav a { position: absolute; top: 66px; font-size: 19px; font-weight: 500; color: var(--white); text-decoration: none; }

  .start-box { position: absolute; left: 98px; top: 224px; width: 325px; height: 323px; border: 2px solid var(--white); padding: 3px; z-index: 2; }
  .start-box-inner { width: 100%; height: 100%; background: var(--form-bg); border: 1px solid #888; padding: 46px 26px 0 26px; }
  .start-box h2 { font-size: 24px; font-weight: 600; color: #222; margin-bottom: 17px; }
  .email-field { display: block; width: 268px; height: 35px; background: var(--white); border: 1px solid #ddd; font: 400 12px "Montserrat", sans-serif; color: #555; padding: 0 13px; line-height: 33px; }
  .consent { margin-top: 17px; font-size: 12px; line-height: 26px; color: var(--form-text); }
  .consent .tick { display: inline-block; width: 10px; height: 10px; background: var(--brand-blue); border-radius: 2px; margin-right: 5px; vertical-align: -1px; }
  .submit-btn { display: block; margin-top: 14px; width: 131px; height: 38px; background: linear-gradient(#1470b0, #1d86cc); color: var(--white); font: 500 17px "Montserrat", sans-serif; text-align: center; line-height: 38px; }

  .headline { position: absolute; left: 483px; top: 330px; width: 600px; text-align: center; color: var(--white); font-size: 41px; font-weight: 700; line-height: 55px; z-index: 2; }

  .stats-band { position: absolute; top: 699px; left: 0; width: 1200px; height: 164px; background: var(--brand-blue); }
  .stat { position: absolute; top: 623px; width: 220px; text-align: center; z-index: 2; }
  .stat svg { display: block; margin: 0 auto; }
  .stat-number { position: absolute; top: 0; left: 0; width: 220px; height: 146px; line-height: 146px; font-size: 31px; font-weight: 700; color: var(--number-blue); }
  .stat-label { margin-top: 20px; color: var(--white); font-size: 17px; font-weight: 500; line-height: 22px; }

  .site-footer { position: absolute; top: 863px; left: 0; width: 1200px; height: 186px; background: var(--footer-bg); color: var(--white); text-align: center; }
  .social { display: flex; justify-content: center; gap: 9px; margin-top: 28px; }
  .social span { width: 34px; height: 34px; border: 2px solid var(--white); border-radius: 50%; }
  .footer-nav { margin-top: 17px; font-family: "Open Sans", sans-serif; font-size: 14px; }
  .footer-nav a { color: var(--white); text-decoration: none; }
  .footer-nav .sep { margin: 0 10px; }
  .copyright { margin-top: 18px; font-family: "Open Sans", sans-serif; font-size: 14px; }
</style>
</head>
<body>
  <div class="top-rule"></div>
  <div class="hero-photo" role="img" aria-label="Blurred photo of a hand holding a smartphone, warm bokeh lights in the background"></div>

  <header class="site-header">
    <div class="brand"><span class="brand-dot"></span><span class="brand-name">Checkora</span></div>
    <nav class="main-nav">
      <a href="#" style="left:543px">Home</a>
      <a href="#" style="left:663px">About</a>
      <a href="#" style="left:779px">Results</a>
      <a href="#" style="left:913px">How</a>
      <a href="#" style="left:1015px">Free Trial</a>
    </nav>
  </header>

  <section class="start-box">
    <div class="start-box-inner">
      <h2>START HERE</h2>
      <div class="email-field">Email Address</div>
      <p class="consent"><span class="tick"></span>"Yes, I have read and agree to the Privacy Policy and agree to receive email marketing from Plumora88'</p>
      <div class="submit-btn">SUBMIT</div>
    </div>
  </section>

  <h1 class="headline">Transform Retail execution<br>with a simple photo</h1>

  <div class="stats-band"></div>

  <div class="stat" style="left:90px">
    <svg width="146" height="146" viewBox="0 0 146 146"><circle cx="73" cy="73" r="69" fill="none" stroke="#fff" stroke-width="6"/><circle cx="73" cy="73" r="60" fill="var(--ring-fill)" stroke="var(--ring-track)" stroke-width="6"/><circle cx="73" cy="73" r="60" fill="none" stroke="#2a2a30" stroke-width="6" stroke-dasharray="270 377" transform="rotate(160 73 73)"/></svg>
    <div class="stat-number">2.2m</div>
    <p class="stat-label">Photos Reviewed<br>Last year</p>
  </div>
  <div class="stat" style="left:343px">
    <svg width="146" height="146" viewBox="0 0 146 146"><circle cx="73" cy="73" r="69" fill="none" stroke="#fff" stroke-width="6"/><circle cx="73" cy="73" r="60" fill="var(--ring-fill)" stroke="var(--ring-track)" stroke-width="6"/><circle cx="73" cy="73" r="60" fill="none" stroke="#2a2a30" stroke-width="6" stroke-dasharray="150 377" transform="rotate(150 73 73)"/><circle cx="73" cy="73" r="60" fill="none" stroke="var(--brand-blue)" stroke-width="6" stroke-dasharray="150 377" transform="rotate(-60 73 73)"/></svg>
    <div class="stat-number">5p</div>
    <p class="stat-label">From per Photo<br>Reviewd</p>
  </div>
  <div class="stat" style="left:604px">
    <svg width="146" height="146" viewBox="0 0 146 146"><circle cx="73" cy="73" r="69" fill="none" stroke="#fff" stroke-width="6"/><circle cx="73" cy="73" r="60" fill="var(--ring-fill)" stroke="var(--brand-blue)" stroke-width="6"/><circle cx="73" cy="73" r="60" fill="none" stroke="#2a2a30" stroke-width="6" stroke-dasharray="120 377" transform="rotate(190 73 73)"/></svg>
    <div class="stat-number">97.2%</div>
    <p class="stat-label">Average Compliance</p>
  </div>
  <div class="stat" style="left:880px">
    <svg width="146" height="146" viewBox="0 0 146 146"><circle cx="73" cy="73" r="69" fill="none" stroke="#fff" stroke-width="6"/><circle cx="73" cy="73" r="60" fill="var(--ring-fill)" stroke="var(--ring-track)" stroke-width="6"/><circle cx="73" cy="73" r="60" fill="none" stroke="#173a3e" stroke-width="6" stroke-dasharray="180 377" transform="rotate(200 73 73)"/><circle cx="73" cy="73" r="60" fill="none" stroke="var(--brand-blue)" stroke-width="6" stroke-dasharray="110 377" transform="rotate(-30 73 73)"/></svg>
    <div class="stat-number">3-8%</div>
    <p class="stat-label">Sales Increase</p>
  </div>

  <footer class="site-footer">
    <div class="social" aria-label="Social links"><span></span><span></span><span></span><span></span></div>
    <p class="footer-nav"><a href="#">Home</a><span class="sep">|</span><a href="#">About</a><span class="sep">|</span><a href="#">Results</a><span class="sep">|</span><a href="#">How</a><span class="sep">|</span><a href="#">Free trail</a></p>
    <p class="copyright">Copyrights © 2018, Checkora. All rights reserved.&nbsp; Sitemap | Terms | Privacy</p>
  </footer>
</body>
</html>
```